Business Card Design (NEW FILES)

ATTENTION: New vector files are available. Please update your design to reflect/use the new (better resolution) logo images.

Seeking a unique and professional business card design for a commercial drone photography/videography business. The layout should feature
the logo (attached) and include the following information:
Owen Tarrick
614-502-7738
www.skylarkreelworks.example
NRD Certified Remote Pilot

Owen Tarrick

```html
<!DOCTYPE html>
<html lang="en">
<head>
<meta charset="utf-8">
<title>Skylark Reelworks – Business Card</title>
<link href="https://fonts.googleapis.com/css2?family=Open+Sans:wght@400;600;700&display=swap" rel="stylesheet">
<style>
  :root {
    --page-bg: #d8d1c6;
    --card-bg: #ece5da;
    --navy: #14173f;
    --navy-deep: #0e1033;
    --orange: #e0793a;
    --bar-gold: #b9772f;
    --ink: #23264a;
    --cream: #efe6d8;
  }
  html, body {
    margin: 0;
    padding: 0;
    width: 1200px;
    height: 1046px;
    overflow: hidden;
    background: var(--page-bg);
    font-family: "Open Sans", Arial, sans-serif;
  }
  .card {
    position: absolute;
    left: 60px;
    top: 230px;
    width: 1080px;
    height: 586px;
    border-radius: 30px;
    background: var(--card-bg);
    overflow: hidden;
    box-shadow: 0 10px 30px rgba(40, 30, 20, 0.18);
  }
  .card-waves {
    position: absolute;
    inset: 0;
  }
  .brand {
    position: absolute;
    left: 47px;
    top: 62px;
    display: flex;
    align-items: center;
    gap: 16px;
  }
  .brand-dot {
    width: 22px;
    height: 22px;
    border-radius: 50%;
    background: var(--orange);
  }
  .brand-name {
    font-size: 44px;
    font-weight: 600;
    color: var(--navy);
    letter-spacing: 0.5px;
    line-height: 1;
  }
  .person {
    position: absolute;
    right: 43px;
    top: 52px;
    text-align: right;
  }
  .person-name {
    font-size: 47px;
    font-weight: 700;
    color: var(--navy);
    line-height: 1.1;
  }
  .person-name .first { color: var(--orange); }
  .person-role {
    font-size: 24px;
    font-weight: 600;
    color: var(--ink);
    margin-top: 2px;
  }
  .accent-bar {
    position: absolute;
    right: 2px;
    top: 48px;
    width: 32px;
    height: 95px;
    background: var(--bar-gold);
  }
  .contacts {
    position: absolute;
    left: 40px;
    top: 352px;
    margin: 0;
    padding: 0;
    list-style: none;
  }
  .contacts li {
    display: flex;
    align-items: center;
    gap: 18px;
    height: 36px;
    font-size: 26px;
    font-weight: 600;
    color: var(--ink);
  }
  .contacts svg { width: 24px; height: 24px; flex: none; }
  .drone-art {
    position: absolute;
    left: 620px;
    top: 296px;
    width: 453px;
    height: 166px;
    border-radius: 12px;
    background: linear-gradient(180deg, rgba(20,23,63,0.55) 0%, rgba(20,23,63,0.9) 70%, rgba(224,121,58,0.35) 100%);
  }
  .credentials {
    position: absolute;
    left: 620px;
    top: 474px;
    width: 453px;
    text-align: center;
    color: var(--cream);
    font-size: 25px;
    line-height: 34px;
  }
</style>
</head>
<body>
  <main class="card">
    <svg class="card-waves" viewBox="0 0 1080 586" width="1080" height="586" aria-hidden="true">
      <path d="M0,505 C150,560 350,572 550,500 C700,440 790,368 900,360 C1000,353 1060,378 1080,392 L1080,586 L0,586 Z" fill="var(--navy)"/>
      <path d="M0,452 C60,525 250,575 415,560" fill="none" stroke="var(--orange)" stroke-width="8"/>
    </svg>

    <div class="brand">
      <span class="brand-dot"></span>
      <span class="brand-name">Skylark Reelworks</span>
    </div>

    <div class="person">
      <div class="person-name"><span class="first">Owen</span> Tarrick</div>
      <div class="person-role">Owner</div>
    </div>
    <div class="accent-bar"></div>

    <ul class="contacts">
      <li>
        <svg viewBox="0 0 24 24"><path d="M6.6 10.8a15.1 15.1 0 0 0 6.6 6.6l2.2-2.2c.3-.3.7-.4 1-.2 1.1.4 2.3.6 3.6.6.6 0 1 .4 1 1V20c0 .6-.4 1-1 1A17 17 0 0 1 3 4c0-.6.4-1 1-1h3.5c.6 0 1 .4 1 1 0 1.3.2 2.5.6 3.6.1.3 0 .7-.2 1z" fill="var(--orange)"/></svg>
        614-502-7738
      </li>
      <li>
        <svg viewBox="0 0 24 24"><circle cx="12" cy="12" r="10" fill="var(--orange)"/><path d="M2 12h20M12 2c3 3 3 17 0 20M12 2c-3 3-3 17 0 20" fill="none" stroke="var(--card-bg)" stroke-width="1.4"/></svg>
        www.skylarkreelworks.example
      </li>
      <li>
        <svg viewBox="0 0 24 24"><rect x="2" y="6" width="20" height="14" rx="1.5" fill="var(--orange)"/><path d="M2 7l10 7 10-7" fill="none" stroke="var(--card-bg)" stroke-width="1.6"/></svg>
        info@skylarkreelworks.example
      </li>
    </ul>

    <div class="drone-art" role="img" aria-label="Illustration of a quadcopter drone carrying a camera"></div>

    <div class="credentials">
      NRD Certified Remote Pilot<br>
      Fully Insured
    </div>
  </main>
</body>
</html>
```